Website redesign www.marigoldlawpc.com law firm site

Need to redesign the website that I currently have to look more modern and professional. Would also like to be able to make updates and post without having a huge hassle. See current www.marigoldlawpc.com. I just think that it looks very immature and it's very templated there's no ability for me to make posts or Add links or anything like that

Target Market(s)

California people looking for a powerhouse attorney in

Industry/Entity Type

Legal

Number of Pages Required

3 page

Font styles to use
Serif
Sans Serif

Colors
ec1f27
000000
ffffff

Requirements
Must have
• Must be mobile friendly. Must look professional and have ability to post links to other websites. Must have ability to post blogs or articles. Would like to be able to read my FeeTrove account and also have the ability to upload forms for people to download
Nice to have
• Simple design easy to use and not cluttered with too much text

```html
<!DOCTYPE html>
<html lang="en">
<head>
<meta charset="utf-8">
<title>Marigold Law, P.C. — Chico California Attorney</title>
<link rel="stylesheet" href="https://fonts.googleapis.com/css2?family=Montserrat:wght@400;600;700&family=Open+Sans:wght@400;600;700&family=Lora:ital,wght@0,400;1,400&display=swap">
<style>
:root{
  --red:#ec1f27;
  --black:#000000;
  --white:#ffffff;
  --ink:#1c1c1c;
  --text:#555555;
  --muted:#8a8a8a;
  --line:#e3e3e3;
  --nav:#262626;
  --band:#2e2e2e;
  --footer:#1f1f1f;
  --field:#2b2b2b;
}
*{box-sizing:border-box;margin:0;padding:0}
html,body{width:1200px;height:3158px;overflow:hidden}
body{background:var(--white);font-family:"Open Sans",Arial,sans-serif;color:var(--text);position:relative}
.abs{position:absolute}
.heading{font-family:"Montserrat",Arial,sans-serif;font-weight:700;color:var(--ink);text-transform:uppercase;text-align:center;letter-spacing:.5px}
.lede{font-family:"Lora",Georgia,serif;font-style:italic;font-size:13px;line-height:21px;color:var(--muted);text-align:center}
.btn-red{background:var(--red);color:var(--white);font-family:"Montserrat",Arial,sans-serif;font-weight:600;font-size:11px;text-transform:uppercase;display:flex;align-items:center;justify-content:center;gap:10px}
.btn-outline{border:1px solid #d8d8d8;background:var(--white);color:var(--ink);font-family:"Montserrat",Arial,sans-serif;font-weight:600;font-size:11px;text-transform:uppercase;display:flex;align-items:center;justify-content:center}

/* hero */
.hero{left:0;top:0;width:1200px;height:500px;background:radial-gradient(ellipse at 45% 35%,#5a5a5a 0%,#2c2c2c 45%,#0e0e0e 100%)}
.brand{left:242px;top:30px;font-family:"Montserrat",Arial,sans-serif;font-weight:600;color:var(--white);font-size:22px;line-height:28px}
.hero-call{left:785px;top:34px;font-family:"Montserrat",Arial,sans-serif;font-weight:700;color:var(--white);font-size:15px}
.hero-serve{left:822px;top:56px;font-size:8px;color:#ddd;font-weight:700;letter-spacing:.3px}
.hero-title{left:0;top:230px;width:1200px;font-family:"Montserrat",Arial,sans-serif;font-weight:600;color:var(--white);font-size:33px;line-height:43px;text-align:center;text-transform:uppercase;letter-spacing:1px}
.hero-sub{left:0;top:325px;width:1200px;text-align:center;font-family:"Lora",Georgia,serif;font-style:italic;color:#e6e6e6;font-size:13px}
.hero-btn{left:505px;top:377px;width:194px;height:34px}
.arrow-dot{width:38px;height:38px;border-radius:50%;background:#111;display:flex;align-items:center;justify-content:center}

/* nav */
.nav{left:0;top:500px;width:1200px;height:56px;background:var(--nav)}
.nav ul{list-style:none;display:flex;position:absolute;left:238px;top:0;height:56px;align-items:center}
.nav li{font-family:"Montserrat",Arial,sans-serif;font-size:11px;color:#ddd;padding:0 14px 0 13px}
.nav li.active{color:var(--red)}

/* welcome */
.wordcloud{left:236px;top:716px;width:318px;height:180px;background:radial-gradient(ellipse at 50% 50%,#c9a9a9 0%,#ead9d9 55%,#fff 85%)}
.intro-name{left:568px;top:708px;font-family:"Montserrat",Arial,sans-serif;font-weight:600;color:var(--ink);font-size:15px;line-height:20px}
.intro-copy{left:568px;top:750px;width:410px;font-size:8.5px;line-height:14px;color:#444}

/* CTA band */
.cta{left:0;top:941px;width:1200px;height:105px;background:var(--band)}
.cta-text{left:288px;top:38px;font-family:"Montserrat",Arial,sans-serif;font-weight:700;color:var(--white);font-size:19px;letter-spacing:.5px}
.cta-btn{left:716px;top:36px;width:194px;height:34px}

/* practice */
.practice-card{top:1215px;width:173px;height:118px;background:var(--white);border:1px solid var(--line);box-shadow:0 2px 4px rgba(0,0,0,.06);text-align:center}
.practice-card svg.ic{margin-top:26px}
.practice-card h3{font-family:"Montserrat",Arial,sans-serif;font-weight:600;font-size:10px;color:var(--ink);margin-top:8px}
.practice-card .go{margin-top:14px}

/* testimonials */
.testimonials{left:0;top:1470px;width:1200px;height:218px;background:linear-gradient(180deg,#6f6f6f 0%,#555 55%,#3d3d3d 100%)}

/* blog */
.post{top:1888px;width:229px;height:340px;background:var(--white);border:1px solid var(--line);box-shadow:0 2px 5px rgba(0,0,0,.07)}
.post .photo{width:100%;height:150px}
.post .meta{display:flex;justify-content:space-between;padding:8px 10px 0;font-size:8px;color:var(--muted);border-top:1px solid var(--line);margin:0}
.post h4{font-family:"Montserrat",Arial,sans-serif;font-weight:600;font-size:12.5px;line-height:17px;padding:22px 18px 0;color:var(--ink)}
.post h4.hot{color:var(--red)}
.post .rule{width:12px;border-top:1px solid #bbb;margin:12px 18px}
.post p{font-size:8.5px;line-height:14px;padding:0 18px;color:#777}
.post .go{position:absolute;left:93px;bottom:-6px;width:36px;height:18px;display:flex;align-items:center;justify-content:center;background:var(--white);border:1px solid var(--line)}
.post .go.hot{background:var(--red);border-color:var(--red)}

/* contact */
.contact{left:0;top:2375px;width:1200px;height:420px;background:radial-gradient(ellipse at 40% 40%,#2e2e2e 0%,#161616 60%,#0b0b0b 100%)}
.label{font-family:"Montserrat",Arial,sans-serif;font-weight:600;color:var(--white);font-size:12px}
.field{background:var(--field);border:1px solid #3d3d3d;font-size:9px;color:#888;display:flex;align-items:center;justify-content:space-between;padding:0 12px}
.send{left:794px;top:235px;width:166px;height:116px;flex-direction:column;font-size:12px;gap:8px}

/* footer */
.footer{left:0;top:2795px;width:1200px;height:363px;background:var(--footer)}
.foot-title{font-family:"Montserrat",Arial,sans-serif;font-weight:600;color:var(--white);font-size:14px}
.foot-menu{list-style:none}
.foot-menu li{font-size:9px;color:#ccc;line-height:21px;display:flex;align-items:center;gap:10px}
.foot-menu li.active{color:var(--red)}
.foot-about{font-size:9px;line-height:15px;color:#bbb}
.contact-row{display:flex;gap:14px;font-size:8.5px;line-height:13px;color:#ccc;margin-bottom:14px}
.contact-row b{color:var(--white)}
.social{width:20px;height:20px;background:#e6e6e6;border-radius:3px}
</style>
</head>
<body>

<header class="abs hero" role="img" aria-label="Black and white photograph of attorneys in suits shaking hands at a meeting">
  <div class="abs brand">Marigold Law, P.C.</div>
  <div class="abs hero-call">Call Us: (555) 014-2290</div>
  <div class="abs hero-serve">SERVING THE STATE OF NEW YORK</div>
  <div class="abs arrow-dot" style="left:20px;top:254px">
    <svg width="10" height="10" viewBox="0 0 10 10"><path d="M7 1 3 5l4 4" fill="none" stroke="#fff" stroke-width="1.6"/></svg>
  </div>
  <div class="abs arrow-dot" style="left:1140px;top:254px">
    <svg width="10" height="10" viewBox="0 0 10 10"><path d="M3 1l4 4-4 4" fill="none" stroke="#ec1f27" stroke-width="1.6"/></svg>
  </div>
  <h1 class="abs hero-title">Curabitur non eratus<br>egestas luctus. Cras ac sapien</h1>
  <p class="abs hero-sub">Phasellus sollicitudin augue tempus, varius lorem id, pellentesque</p>
  <div class="abs btn-red hero-btn">Free Case Evaluation
    <svg width="13" height="12" viewBox="0 0 13 12"><path d="M5 1h6v10H5" fill="none" stroke="#fff" stroke-width="1.6"/><path d="M1 6h6M5 3.5 7.5 6 5 8.5" fill="none" stroke="#fff" stroke-width="1.6"/></svg>
  </div>
</header>

<nav class="abs nav">
  <ul>
    <li class="active">Home</li><li>Attorney Profile</li><li>Practice Areas</li><li>Client Reviews</li><li>Links</li><li>Contact Us</li>
  </ul>
  <svg class="abs" style="left:953px;top:21px" width="14" height="14" viewBox="0 0 14 14"><circle cx="6" cy="6" r="4.5" fill="none" stroke="#ec1f27" stroke-width="1.8"/><path d="M9.3 9.3 13 13" stroke="#ec1f27" stroke-width="2"/></svg>
</nav>

<h2 class="abs heading" style="left:0;top:598px;width:1200px;font-size:21px">Welcome to Marigold Law</h2>
<p class="abs lede" style="left:0;top:633px;width:1200px">Lorem ipsum dolor sit amet, consectetur adipiscing elit. Nulla felis tellus, tristique nec dignissim quis,<br>Duis consectetur blandit tortor, quis viverra ipsum dapibus et. Sed auctor sit amet nisl ac dapibus. Mauris nulla lectus, male</p>
<div class="abs" style="left:300px;top:684px;width:600px;height:6px;box-shadow:0 4px 6px -4px rgba(0,0,0,.15)"></div>
<div class="abs wordcloud" role="img" aria-label="Word cloud illustration of legal terms such as criminal, law, justice and legal"></div>
<div class="abs intro-name">Marigold Law, P.C.<br>Chico California Attorney</div>
<p class="abs intro-copy">Find the big firm style legal counsel you can work with in your hometown region at Marigold Law P.C., in Chico, CA. Attorney Dana R. Marigold, Esq., offers a boutique law firm opportunity for clients who want to enjoy all the advantages of her broad legal experience and education. She works closely with clients, and has the knowledge of many areas of law to apply to your situation. This is very helpful when it is necessary to incorporate those different areas of law practice into creating a winning argument for your unique case.</p>
<div class="abs btn-outline" style="left:568px;top:862px;width:206px;height:34px">More About Us</div>

<section class="abs cta">
  <div class="abs cta-text">WE ARE HERE TO PROVIDE LEGAL HELP</div>
  <div class="abs btn-red cta-btn">Free Case Evaluation
    <svg width="13" height="12" viewBox="0 0 13 12"><path d="M5 1h6v10H5" fill="none" stroke="#fff" stroke-width="1.6"/><path d="M1 6h6M5 3.5 7.5 6 5 8.5" fill="none" stroke="#fff" stroke-width="1.6"/></svg>
  </div>
</section>

<h2 class="abs heading" style="left:0;top:1092px;width:1200px;font-size:21px">Practice Areas</h2>
<p class="abs lede" style="left:0;top:1127px;width:1200px">Lorem ipsum dolor sit amet, consectetur adipiscing elit. Nulla felis tellus, tristique nec dignissim quis,<br>Duis consectetur blandit tortor, quis viverra ipsum dapibus et. Sed auctor sit amet nisl ac dapibus. Mauris nulla lectus, male</p>
<svg class="abs" style="left:148px;top:1250px" width="20" height="44" viewBox="0 0 20 44"><path d="M18 2 2 22l16 20" fill="none" stroke="#e0e0e0" stroke-width="2"/></svg>
<svg class="abs" style="left:1015px;top:1250px" width="20" height="44" viewBox="0 0 20 44"><path d="M2 2l16 20L2 42" fill="none" stroke="#e0e0e0" stroke-width="2"/></svg>

<div class="abs practice-card" style="left:242px">
  <svg class="ic" width="34" height="30" viewBox="0 0 34 30"><path d="M17 2 2 15h4v13h8v-8h6v8h8V15h4z" fill="#111"/></svg>
  <h3>REAL ESTATE LAW</h3>
  <svg class="go" width="12" height="11" viewBox="0 0 13 12"><path d="M5 1h6v10H5" fill="none" stroke="#111" stroke-width="1.6"/><path d="M1 6h6M5 3.5 7.5 6 5 8.5" fill="none" stroke="#111" stroke-width="1.6"/></svg>
</div>
<div class="abs practice-card" style="left:425px">
  <svg class="ic" width="36" height="30" viewBox="0 0 36 30"><circle cx="18" cy="8" r="6" fill="#111"/><circle cx="7" cy="11" r="4" fill="#111"/><circle cx="29" cy="11" r="4" fill="#111"/><path d="M8 28c0-8 4-12 10-12s10 4 10 12z" fill="#111"/><path d="M0 27c0-6 3-9 7-9 2 0 3 1 4 2-2 2-3 4-3 7zM36 27c0-6-3-9-7-9-2 0-3 1-4 2 2 2 3 4 3 7z" fill="#111"/></svg>
  <h3>FAMILY LAW</h3>
  <svg class="go" width="12" height="11" viewBox="0 0 13 12"><path d="M5 1h6v10H5" fill="none" stroke="#111" stroke-width="1.6"/><path d="M1 6h6M5 3.5 7.5 6 5 8.5" fill="none" stroke="#111" stroke-width="1.6"/></svg>
</div>
<div class="abs practice-card" style="left:609px">
  <svg class="ic" width="34" height="30" viewBox="0 0 34 30"><rect x="11" y="2" width="12" height="6" rx="1" fill="none" stroke="#111" stroke-width="2.4"/><rect x="2" y="8" width="30" height="20" rx="2" fill="#111"/></svg>
  <h3>BUSINESS LAW</h3>
  <svg class="go" width="12" height="11" viewBox="0 0 13 12"><path d="M5 1h6v10H5" fill="none" stroke="#111" stroke-width="1.6"/><path d="M1 6h6M5 3.5 7.5 6 5 8.5" fill="none" stroke="#111" stroke-width="1.6"/></svg>
</div>
<div class="abs practice-card" style="left:793px">
  <svg class="ic" width="34" height="30" viewBox="0 0 34 30"><circle cx="11" cy="19" r="7" fill="none" stroke="#111" stroke-width="3"/><circle cx="23" cy="9" r="6" fill="none" stroke="#111" stroke-width="3"/><path d="M15 14l3-2" stroke="#111" stroke-width="3"/></svg>
  <h3>CRIMINAL LAW</h3>
  <svg class="go" width="12" height="11" viewBox="0 0 13 12"><path d="M5 1h6v10H5" fill="none" stroke="#111" stroke-width="1.6"/><path d="M1 6h6M5 3.5 7.5 6 5 8.5" fill="none" stroke="#111" stroke-width="1.6"/></svg>
</div>
<div class="abs btn-outline" style="left:495px;top:1380px;width:206px;height:32px">All Practice Areas</div>

<section class="abs testimonials" role="img" aria-label="Muted photograph of a business meeting silhouetted against bright windows">
  <h2 class="abs heading" style="left:0;top:32px;width:1200px;font-size:19px;color:#fff">Testimonials</h2>
  <div class="abs" style="left:0;top:86px;width:1200px;text-align:center;font-family:'Lora',Georgia,serif;font-weight:400;color:#fff;font-size:12px">Exceeded Our Expectations</div>
  <p class="abs lede" style="left:240px;top:108px;width:720px;color:#eee;font-size:10.5px;line-height:17px">Marigold Law has met and exceeded our expectations in assisting our company with our real estate legal needs. In an area of law where the rules are ever-changing, we simply could not navigate our company effectively without their help.</p>
  <div class="abs lede" style="left:0;top:152px;width:1200px;color:#ddd;font-size:10px">Alder Commercial</div>
  <div class="abs" style="left:597px;top:190px;width:6px;height:6px;border-radius:50%;background:#ddd"></div>
</section>

<h2 class="abs heading" style="left:0;top:1756px;width:1200px;font-size:21px">Latest Blog</h2>
<p class="abs lede" style="left:0;top:1794px;width:1200px">We are a full service, general practice law firm, but we specialize in the areas of residential<br>and commercial real estate transactions and litigation and commercial transactions and litigation.</p>
<div class="abs" style="left:300px;top:1840px;width:600px;height:6px;box-shadow:0 4px 6px -4px rgba(0,0,0,.15)"></div>

<article class="abs post" style="left:240px">
  <div class="photo" role="img" aria-label="Photograph of a lawyer shaking hands with a client across a desk" style="background:linear-gradient(135deg,#6b6b6b,#3a3a3a 60%,#9a9a9a)"></div>
  <div class="meta"><span>Litigation</span><span>22 MAY 2016</span></div>
  <h4 class="hot">Adipiscit elit voluptatem sed consectutor adipiscit elit</h4>
  <div class="rule"></div>
  <p>Sed ut perspiciatis unde omnis iste natus error sit voluptatem accusantium doloremque laudantium, totam rem aperiam, eaque ipsa.</p>
  <div class="go hot"><svg width="10" height="9" viewBox="0 0 13 12"><path d="M5 1h6v10H5" fill="none" stroke="#fff" stroke-width="1.8"/><path d="M1 6h6M5 3.5 7.5 6 5 8.5" fill="none" stroke="#fff" stroke-width="1.8"/></svg></div>
</article>
<article class="abs post" style="left:486px">
  <div class="photo" role="img" aria-label="Photograph of hands signing a contract with a pen" style="background:linear-gradient(135deg,#c8ced6,#8f9aa6 55%,#e4e7ea)"></div>
  <div class="meta"><span>Litigation</span><span>22 MAY 2016</span></div>
  <h4>Partis vivarum magna elit voluptatem sed do</h4>
  <div class="rule"></div>
  <p>Sed ut perspiciatis unde omnis iste natus error sit voluptatem accusantium doloremque laudantium, totam rem aperiam, eaque ipsa.</p>
  <div class="go"><svg width="10" height="9" viewBox="0 0 13 12"><path d="M5 1h6v10H5" fill="none" stroke="#111" stroke-width="1.8"/><path d="M1 6h6M5 3.5 7.5 6 5 8.5" fill="none" stroke="#111" stroke-width="1.8"/></svg></div>
</article>
<article class="abs post" style="left:733px">
  <div class="photo" role="img" aria-label="Photograph of a team gathered around a conference table" style="background:linear-gradient(135deg,#b79a7c,#7d6650 55%,#d9c8b4)"></div>
  <div class="meta"><span>Litigation</span><span>22 MAY 2016</span></div>
  <h4>Velup stormis vivus magna elit consectetur dolor</h4>
  <div class="rule"></div>
  <p>Sed ut perspiciatis unde omnis iste natus error sit voluptatem accusantium doloremque laudantium, totam rem aperiam, eaque ipsa.</p>
  <div class="go"><svg width="10" height="9" viewBox="0 0 13 12"><path d="M5 1h6v10H5" fill="none" stroke="#111" stroke-width="1.8"/><path d="M1 6h6M5 3.5 7.5 6 5 8.5" fill="none" stroke="#111" stroke-width="1.8"/></svg></div>
</article>
<div class="abs btn-outline" style="left:497px;top:2267px;width:206px;height:32px">All Latest Blog</div>

<section class="abs contact" role="img" aria-label="Dark photograph of a desk with a gavel and papers">
  <h2 class="abs heading" style="left:0;top:74px;width:1200px;font-size:19px;color:#fff">Contact Us</h2>
  <div class="abs label" style="left:238px;top:126px">Name</div>
  <div class="abs label" style="left:608px;top:126px">Email</div>
  <div class="abs field" style="left:238px;top:149px;width:356px;height:38px"><span>Name</span>
    <svg width="10" height="10" viewBox="0 0 10 10"><circle cx="5" cy="3" r="2.5" fill="#ccc"/><path d="M0 10c0-3 2-5 5-5s5 2 5 5z" fill="#ccc"/></svg></div>
  <div class="abs field" style="left:608px;top:149px;width:352px;height:38px"><span>Email address...</span>
    <svg width="11" height="9" viewBox="0 0 11 9"><rect width="11" height="9" fill="#ccc"/><path d="M0 0l5.5 5L11 0" fill="none" stroke="#2b2b2b"/></svg></div>
  <div class="abs label" style="left:238px;top:212px">Message</div>
  <div class="abs field" style="left:238px;top:235px;width:537px;height:116px;align-items:flex-start;padding-top:12px"><span>Briefly describe your case...</span>
    <svg width="10" height="10" viewBox="0 0 10 10"><path d="M1 9l1-3 5-5 2 2-5 5z" fill="#ccc"/></svg></div>
  <div class="abs btn-red send">Send Message
    <svg width="20" height="18" viewBox="0 0 13 12"><path d="M5 1h6v10H5" fill="none" stroke="#fff" stroke-width="1.6"/><path d="M1 6h6M5 3.5 7.5 6 5 8.5" fill="none" stroke="#fff" stroke-width="1.6"/></svg>
  </div>
</section>

<footer class="abs footer">
  <div class="abs foot-title" style="left:238px;top:77px">MENU</div>
  <ul class="abs foot-menu" style="left:242px;top:102px">
    <li class="active">→ <span>Home</span></li><li>→ <span>Attorney Profile</span></li><li>→ <span>Practice Areas</span></li><li>→ <span>Client Reviews</span></li><li>→ <span>Links</span></li><li>→ <span>Contact Us</span></li>
  </ul>
  <div class="abs" style="left:390px;top:78px;height:170px;border-left:1px solid #333"></div>
  <div class="abs foot-title" style="left:432px;top:77px">ABOUT</div>
  <p class="abs foot-about" style="left:432px;top:104px;width:300px">Marigold Law, P.C. provides experienced, compassionate legal guidance and representation to businesses and individuals in the areas of business law, real estate law, bankruptcy, family law, criminal law, civil litigation, unlawful detainer, and legal document preparation. Located in Chico, California, we serve clients throughout Northern California including Butte County, Tehama County, Plumas County, Glenn County, Colusa County, Sutter County, Yuba County, Sierra County and Nevada County.</p>
  <div class="abs" style="left:760px;top:78px;height:170px;border-left:1px solid #333"></div>
  <div class="abs foot-title" style="left:794px;top:77px">CONTACT INFO</div>
  <div class="abs" style="left:796px;top:105px;width:200px">
    <div class="contact-row"><svg width="8" height="11" viewBox="0 0 8 11"><path d="M4 0a4 4 0 0 1 4 4c0 3-4 7-4 7S0 7 0 4a4 4 0 0 1 4-4z" fill="#ccc"/><circle cx="4" cy="4" r="1.5" fill="#1f1f1f"/></svg><span>Marigold Law, P.C. Office<br>48 Orchard Lane<br>Suite 310<br>Chico, CA 95900</span></div>
    <div class="contact-row" style="margin-top:14px"><svg width="10" height="10" viewBox="0 0 10 10"><path d="M2 0l2 2-1 2 3 3 2-1 2 2-2 2C4 10 0 6 0 2z" fill="#ccc"/></svg><span><b>Phone</b> (555) 014-2290</span></div>
    <div class="contact-row"><svg width="10" height="10" viewBox="0 0 10 10"><rect x="1" y="3" width="8" height="5" fill="#ccc"/><rect x="3" y="0" width="4" height="3" fill="#ccc"/></svg><span><b>Fax</b> (555) 014-2291</span></div>
    <div class="contact-row"><svg width="10" height="8" viewBox="0 0 11 9"><rect width="11" height="9" fill="#ccc"/><path d="M0 0l5.5 5L11 0" fill="none" stroke="#1f1f1f"/></svg><span><b>Email</b> office@marigoldlawpc.com</span></div>
  </div>
  <div class="abs" style="left:1021px;top:152px;width:30px;height:30px;border:1px solid #444;display:flex;align-items:center;justify-content:center">
    <svg width="10" height="6" viewBox="0 0 10 6"><path d="M1 5l4-4 4 4" fill="none" stroke="#ccc" stroke-width="1.4"/></svg>
  </div>
  <div class="abs" style="left:0;top:286px;width:1200px;border-top:1px solid #2c2c2c"></div>
  <div class="abs" style="left:553px;top:300px;display:flex;gap:14px">
    <div class="social" aria-label="Social profile"></div><div class="social" aria-label="Social profile"></div><div class="social" aria-label="Social profile"></div>
  </div>
  <div class="abs" style="left:0;top:333px;width:1200px;text-align:center;font-size:8.5px;color:#aaa">© All rights reserved - Marigold Law 2018 - Terms &amp; Conditions</div>
</footer>

</body>
</html>
```